Motivational Poster Design Project

I would like to create a poster with some of my favorite quotes to hang in my office. I did a similar project in 2012 and I've uploaded the top 2 designs so you can get a better idea of what I'm looking for. I will provide feedback on your design within 24 hours of receiving it.

The poster must contain the following quotes:

"You’re only given a little spark of madness. You mustn’t lose it.”
- Dorian Fletcher

“The most contrarian thing of all is not to oppose the crowd but to think for yourself.”
- Marcus Olden

"I constantly see people rise in life who are not the smartest, sometimes not even the most diligent, but they are learning machines. They go to bed every night a little wiser than they were when they got up and boy does that help, particularly when you have a long run ahead of you."
- Frankie Dalgarth

“In theory, there’s no difference between theory and practice. But, in practice, there is.”
- Kees R. T. Ter Haverkamp

"At the end of the day, a reactionary life is a normal life. One thing is consistent in every remarkable person: they decide to do something remarkable. Don’t let the world choose who you become."
- Rohan Kapadia

“It usually takes 3-4 months to try enough that you can do a proper 80/20 analysis, then two months to design systems to scale what *is* working.”
-Ned Yarrow

“Authority is 20 percent given, 80 percent taken.”
- Glenn Mosbacker

“Your actions are consistent with the way the world occurs to you.”
- Dieter Kolbach

Project Deadline Extended
Reason: I am going to be travelling with no access to internet until January 5th, 2015. I am extending the project deadline until 12/31/14 and I'll make a final decision during the 1st week of January.

Target Market(s)

Personal Project

Industry/Entity Type

Learning

Requirements
Must have
• The poster will be 24" high x 36" long and printed on canvas, so the image you create needs to have a resolution of at least 2700 x 3900.
Nice to have
• I don't have an exact vision for how the poster should look, so I am totally open to you using your creativity to develop, arrange and present the content as you'd like.
• That said, I would like an image (photo or posterized image) of the person being quoted along with each quote. I do not have specific images that I would like you to use, so you will need to find the images on your own. The images don't need to be perfect... I am more interested in the poster relating the essence of the quotes and the people being quoted than I am in perfect photographic images of the people being quoted.

```html
<!DOCTYPE html>
<html lang="en">
<head>
<meta charset="utf-8">
<title>Quotes Poster</title>
<link href="https://fonts.googleapis.com/css2?family=Playfair+Display:ital,wght@0,400;0,600;1,400&display=swap" rel="stylesheet">
<style>
  :root {
    --bg-dark: #141210;
    --bg-mid: #3a342e;
    --ink: #f4efe6;
    --chalk: #e8e2d8;
    --name-pink: #efa9c6;
    --name-blue: #8fd2f0;
    --name-cream: #f3e7a2;
    --name-butter: #f6eab0;
    --name-salmon: #f2a78e;
    --name-lime: #d8e88c;
    --name-rose: #f0a2b2;
    --name-lavender: #a9a8e2;
  }
  * { margin: 0; padding: 0; box-sizing: border-box; }
  html, body { width: 800px; height: 1200px; overflow: hidden; background: var(--bg-dark); }
  .poster {
    position: relative;
    width: 800px;
    height: 1200px;
    overflow: hidden;
    background: radial-gradient(ellipse at 50% 45%, var(--bg-mid) 0%, #28231f 55%, var(--bg-dark) 100%);
    font-family: "Playfair Display", Georgia, serif;
    color: var(--ink);
  }
  .backdrop { position: absolute; inset: 0; }
  .quote {
    position: absolute;
    white-space: nowrap;
    font-size: 16px;
    line-height: 1.45;
  }
  .quote .big { font-size: 24px; font-weight: 600; }
  .quote .mid { font-size: 20px; }
  .quote .name { font-style: italic; font-size: 18px; }

  .q-spark { left: 232px; top: 104px; }
  .q-spark .name { color: var(--name-pink); }

  .q-contrarian { left: 274px; top: 232px; }
  .q-contrarian .name { color: var(--name-blue); }

  .q-learning { left: 163px; top: 370px; font-size: 12.5px; line-height: 28px; }
  .q-learning .big { font-size: 18px; }
  .q-learning .name { color: var(--name-cream); font-size: 17px; }

  .q-theory { left: 122px; top: 550px; }
  .q-theory .name { color: var(--name-butter); }

  .q-remarkable { left: 252px; top: 646px; font-size: 12.5px; line-height: 29px; }
  .q-remarkable .big { font-size: 18px; font-weight: 400; }
  .q-remarkable .name { color: var(--name-salmon); font-size: 16px; }

  .q-systems { left: 302px; top: 790px; font-size: 14px; line-height: 29px; }
  .q-systems .big { font-size: 20px; font-weight: 400; }
  .q-systems .name { color: var(--name-lime); font-size: 17px; }

  .q-authority { left: 196px; top: 946px; }
  .q-authority .big { font-weight: 400; }
  .q-authority .name { color: var(--name-rose); }

  .q-actions { left: 254px; top: 1054px; }
  .q-actions .big { font-size: 21px; font-weight: 400; }
  .q-actions .name { color: var(--name-lavender); }
</style>
</head>
<body>
<div class="poster">
  <svg class="backdrop" width="800" height="1200" viewBox="0 0 800 1200" xmlns="http://www.w3.org/2000/svg">
    <defs>
      <radialGradient id="portrait-tone" cx="50%" cy="50%" r="50%">
        <stop offset="0%" stop-color="#9a8f82"/>
        <stop offset="55%" stop-color="#6b6157"/>
        <stop offset="100%" stop-color="#2a2520" stop-opacity="0"/>
      </radialGradient>
    </defs>

    <g class="portraits">
      <circle cx="146" cy="140" r="78" fill="url(#portrait-tone)" role="img" aria-label="Sepia portrait of Dorian Fletcher"/>
      <circle cx="716" cy="284" r="82" fill="url(#portrait-tone)" role="img" aria-label="Sepia portrait of Marcus Olden speaking at a podium"/>
      <circle cx="100" cy="400" r="80" fill="url(#portrait-tone)" role="img" aria-label="Sepia portrait of Frankie Dalgarth"/>
      <circle cx="634" cy="538" r="80" fill="url(#portrait-tone)" role="img" aria-label="Sepia portrait of Kees R. T. Ter Haverkamp"/>
      <circle cx="160" cy="690" r="82" fill="url(#portrait-tone)" role="img" aria-label="Sepia portrait of Rohan Kapadia"/>
      <circle cx="690" cy="840" r="84" fill="url(#portrait-tone)" role="img" aria-label="Sepia portrait of Ned Yarrow"/>
      <circle cx="118" cy="968" r="82" fill="url(#portrait-tone)" role="img" aria-label="Sepia portrait of Glenn Mosbacker in a suit"/>
      <circle cx="630" cy="1092" r="80" fill="url(#portrait-tone)" role="img" aria-label="Sepia portrait of Dieter Kolbach"/>
    </g>

    <g class="chalk-icons" fill="none" stroke="#e8e2d8" stroke-width="1.6" stroke-linecap="round" stroke-linejoin="round">
      <g class="icon-bulb" transform="translate(648 104)">
        <path d="M-10 4 a13 13 0 1 1 20 0 c-3 4 -4 6 -4 10 h-12 c0 -4 -1 -6 -4 -10z"/>
        <path d="M-6 18 h12 M-5 22 h10"/>
        <path d="M-24 -10 l-6 -3 M24 -10 l6 -3 M0 -22 v-7 M-17 -20 l-4 -5 M17 -20 l4 -5"/>
      </g>
      <g class="icon-talk" transform="translate(222 288)">
        <ellipse cx="-12" cy="-16" rx="10" ry="7"/>
        <ellipse cx="14" cy="-20" rx="10" ry="7"/>
        <circle cx="-10" cy="2" r="5"/><circle cx="10" cy="2" r="5"/>
        <path d="M-17 20 l7 -12 l7 12z M3 20 l7 -12 l7 12z"/>
      </g>
      <path class="icon-trend" d="M72 498 l14 -12 l8 8 l12 -16 l8 6 l18 -22 m-8 0 h8 v8"/>
      <g class="icon-pencil" transform="translate(548 514) rotate(-35)">
        <rect x="-7" y="-17" width="14" height="26"/>
        <path d="M-7 9 l7 10 l7 -10"/>
      </g>
      <g class="icon-globe" transform="translate(700 690)">
        <circle r="17"/>
        <ellipse rx="7" ry="17"/>
        <path d="M-17 0 h34 M-14 -9 h28 M-14 9 h28 M-23 -2 a25 25 0 0 0 25 25 M2 23 v9 M-8 32 h20"/>
      </g>
      <g class="icon-chart" transform="translate(220 830)">
        <path d="M0 -30 v60 h66"/>
        <path d="M4 20 l12 -14 l10 8 l12 -18 l10 6 l14 -20"/>
        <path d="M4 24 l14 -8 l12 4 l14 -14 l10 2 l12 -10" stroke-dasharray="3 3"/>
      </g>
      <g class="icon-pen" transform="translate(572 962) rotate(30)">
        <rect x="-4" y="-26" width="8" height="42"/>
        <path d="M-4 16 l4 10 l4 -10"/>
      </g>
    </g>
  </svg>

  <p class="quote q-spark">"You're only given a <span class="big">little spark</span> of madness.<br>You mustn't <span class="mid">lose</span> it." &nbsp;<span class="name">- Dorian Fletcher</span></p>

  <p class="quote q-contrarian">"The <span class="big">most contrarian</span> thing of all<br>is not to oppose the crowd but <span class="big">to think</span><br><span class="big">for yourself</span>." <span class="name">- Marcus Olden</span></p>

  <p class="quote q-learning">"I constantly see people rise in life who are not the <span class="big">smartest</span>, sometimes<br>not even the most <span class="big">diligent</span>, but they are <span class="big">learning machines</span>. They go to bed<br>every night a little <span class="big">wiser</span> than they were when they got up and boy does that help,<br>particularly when you have <span class="big">a long run ahead of you</span>."<br><span class="name">- Frankie Dalgarth</span></p>

  <p class="quote q-theory">"<span class="mid">In theory</span>, there's no difference between theory and practice. But,<br><span class="big">in practice</span>, there is." &nbsp;<span class="name">- Kees R. T. Ter Haverkamp</span></p>

  <p class="quote q-remarkable">"At the end of the day, a reactionary life is a <span class="big">normal life</span>.<br>One thing is consistent in every <span class="big">remarkable person</span>:<br>they decide to do something remarkable. <span class="big">Don't let the</span><br><span class="big">world choose who you become</span>." <span class="name">- Rohan Kapadia</span></p>

  <p class="quote q-systems">"It usually takes <span class="big">3-4 months</span> to try enough<br>that you can do a proper 80/20 analysis, then<br><span class="big">two months</span> to design systems to scale<br><span class="big">what *is* working</span>." <span class="name">- Ned Yarrow</span></p>

  <p class="quote q-authority">"Authority is <span class="big">20</span> percent <span class="big">given</span>,<br><span class="big">80</span> percent <span class="big">taken</span>." &nbsp;<span class="name">- Glenn Mosbacker</span></p>

  <p class="quote q-actions">"Your <span class="big">actions</span> are <span class="big">consistent</span><br>with the way the world occurs to you."<br><span class="name">- Dieter Kolbach</span></p>
</div>
</body>
</html>
```